Every Shelf Set Neatly or ESN Organized needs a business card design. ESN Organized is a professi

We need a business card design that is clean, sharp and conveys a sense of organization. I already have a logo.

Target Market(s)

Families (specifically mothers), small business owners, parents, seniors

Industry/Entity Type

Business

Contact Information for Business Card

My website is www.esnorganized-example.com and my Facebook page is http://www.sociallink-example.com/everyshelfsetneatly. The phone number is 418-552-7094 and I want to be listed as Lorna M. Pelham, Owner

Requirements
Must have
• My logo.

```html
<!DOCTYPE html>
<html lang="en">
<head>
<meta charset="utf-8">
<title>ESN Organized – Business Card</title>
<link rel="stylesheet" href="https://fonts.googleapis.com/css2?family=Montserrat:wght@400;500;600&family=Open+Sans:ital,wght@0,400;0,600;0,700;1,400&display=swap">
<style>
  :root {
    --stage: #eceef1;
    --brand-blue: #0a7fdc;
    --brand-blue-soft: #3d9be6;
    --paper: #ffffff;
    --ink: #1a1a1a;
    --label-ink: #777777;
    --band-soft: #e9eef3;
  }
  * { margin: 0; padding: 0; box-sizing: border-box; }
  html, body {
    width: 1200px; height: 900px; overflow: hidden;
    background: var(--stage);
  }
  .canvas { position: relative; width: 1200px; height: 900px; }

  .presentation-title {
    position: absolute; left: 0; width: 1200px; top: 50px;
    text-align: center;
    font: 400 32px "Open Sans", sans-serif; color: var(--ink);
  }
  .side-label {
    position: absolute;
    font: 400 32px "Open Sans", sans-serif; color: var(--label-ink);
  }
  .side-label--front { left: 922px; top: 260px; }
  .side-label--back { left: 276px; top: 716px; }

  .card {
    position: absolute; border-radius: 6px; overflow: hidden;
    box-shadow: 0 6px 22px rgba(0,0,0,.14);
  }
  .card--front {
    left: 65px; top: 132px; width: 555px; height: 343px;
    background: var(--brand-blue); color: var(--paper);
  }
  .card--back {
    left: 470px; top: 530px; width: 565px; height: 350px;
    background: var(--paper);
  }

  .accent-band { position: absolute; top: 0; bottom: 0; }
  .card--front .accent-band {
    right: 0; width: 156px;
    background: linear-gradient(180deg, var(--brand-blue-soft), var(--brand-blue));
  }
  .card--back .accent-band {
    left: 0; width: 160px;
    background: linear-gradient(180deg, #f4f6f8, var(--band-soft));
  }

  .wordmark {
    display: flex; align-items: center; gap: 10px;
    font-family: "Montserrat", sans-serif; font-weight: 500;
    white-space: nowrap;
  }
  .wordmark__dot { width: 12px; height: 12px; }
  .card--front .wordmark {
    position: absolute; left: 31px; top: 40px;
    font-size: 28px; letter-spacing: 3px; color: var(--paper);
  }
  .card--front .wordmark__dot { background: var(--paper); }
  .card--back .wordmark {
    position: absolute; left: 230px; top: 150px;
    font-size: 30px; letter-spacing: 3px; color: var(--brand-blue);
  }
  .card--back .wordmark__dot { background: var(--brand-blue); }

  .holder { position: absolute; left: 31px; top: 122px; font-family: "Open Sans", sans-serif; }
  .holder__name { font-size: 19px; font-weight: 700; }
  .holder__role { font-size: 14px; margin-top: 1px; }

  .contact-list {
    position: absolute; left: 31px; top: 183px; list-style: none;
    font: 400 15px "Open Sans", sans-serif;
  }
  .contact-list li { display: flex; align-items: center; gap: 8px; height: 23.5px; white-space: nowrap; }
  .contact-list svg { width: 12px; height: 12px; flex: none; fill: var(--paper); }

  .tagline {
    position: absolute; left: 31px; top: 292px;
    font: italic 400 14px "Open Sans", sans-serif;
    white-space: nowrap;
  }
</style>
</head>
<body>
<div class="canvas">
  <div class="presentation-title">Double Side Card</div>
  <div class="side-label side-label--front">&lt;-- Front</div>
  <div class="side-label side-label--back">Back --&gt;</div>

  <section class="card card--front">
    <div class="accent-band" role="img" aria-label="Large decorative brand motif"></div>
    <div class="wordmark"><span class="wordmark__dot"></span>ESN Organized</div>
    <div class="holder">
      <div class="holder__name">Lorna M. Pelham</div>
      <div class="holder__role">Owner</div>
    </div>
    <ul class="contact-list">
      <li>
        <svg viewBox="0 0 12 12"><path d="M2.5 1l2 2.2-1 1.3a7 7 0 0 0 4 4l1.3-1 2.2 2-1.2 1.5C5.6 11 1 6.4 1 2.2z"/></svg>
        418-552-7094
      </li>
      <li>
        <svg viewBox="0 0 12 12"><path d="M1 2.5h10v7H1z"/><path d="M1.5 3l4.5 3.5L10.5 3" stroke="#0a7fdc" stroke-width="1" fill="none"/></svg>
        info@esnorganized-example.com
      </li>
      <li>
        <svg viewBox="0 0 12 12"><circle cx="6" cy="6" r="5"/><path d="M1 6h10M6 1c-2.5 3-2.5 7 0 10M6 1c2.5 3 2.5 7 0 10" stroke="#0a7fdc" stroke-width=".9" fill="none"/></svg>
        www.esnorganized-example.com
      </li>
      <li>
        <svg viewBox="0 0 12 12"><circle cx="6" cy="6" r="5"/></svg>
        social/everyshelfsetneatly
      </li>
    </ul>
    <p class="tagline">Every shelf in its place, every corner set neatly</p>
  </section>

  <section class="card card--back">
    <div class="accent-band" role="img" aria-label="Large decorative brand motif"></div>
    <div class="wordmark"><span class="wordmark__dot"></span>ESN Organized</div>
  </section>
</div>
</body>
</html>
```